Construction company business card

One side to be the logo with the company name, The other side I would like: (Tomas verbick) Project manager 41 barrow crescent hallam 52917306224783(03) 9703 2428Info@gudeljgroup.comAnd then maybe a couple dot points saying what we do:Construction (commercial & industrial) Civil construction

Anything else please contact me!
Maybe curved st one edge of the card

Target Market(s)

Older clientele

Industry/Entity Type

Construction Company

Contact Information for Business Card

Read above

Colors
3277b5
1b1b1b
9d9d9d

Requirements
Must have
• Use my logo on one side
Nice to have
• Read above
Should not have
• Read above

```html
<!DOCTYPE html>
<html lang="en">
<head>
<meta charset="utf-8">
<title>Verbrook Property Group – Business Card</title>
<link href="https://fonts.googleapis.com/css2?family=Roboto:wght@400;500;700;900&display=swap" rel="stylesheet">
<style>
  :root {
    --brand-blue: #2e5d8f;
    --brand-blue-bright: #3277b5;
    --ink: #1b1b1b;
    --grey: #9d9d9d;
    --grey-light: #c9c9c9;
    --card-white: #f4f4f4;
    --backdrop: #e4e4e4;
    --tagline-light: #d6e2ee;
  }
  * { box-sizing: border-box; margin: 0; padding: 0; }
  html, body { width: 1200px; height: 576px; overflow: hidden; }
  body {
    background: var(--backdrop);
    font-family: "Roboto", Arial, sans-serif;
    position: relative;
  }
  .card {
    position: absolute;
    top: 138px;
    height: 294px;
    border-radius: 5px 28px 5px 28px;
    overflow: hidden;
  }

  .card-front {
    left: 80px;
    width: 486px;
    background: var(--brand-blue);
    color: #fff;
  }
  .front-name {
    position: absolute;
    left: 0; right: 30px;
    top: 107px;
    text-align: center;
    font-weight: 700;
    color: #fff;
    line-height: 1;
  }
  .front-name .word-main { display: block; font-size: 48px; letter-spacing: 7px; margin-right: -7px; }
  .front-name .word-sub { display: block; font-size: 17px; letter-spacing: 8.4px; margin-right: -8.4px; margin-top: 5px; }
  .front-tagline {
    position: absolute;
    left: 0; right: 0;
    top: 262px;
    text-align: center;
    font-size: 13px;
    color: var(--tagline-light);
  }

  .card-back {
    left: 602px;
    width: 482px;
    background: var(--card-white);
    color: var(--ink);
  }
  .brand-dot {
    position: absolute;
    left: 83px;
    top: 68px;
    width: 82px; height: 82px;
    border-radius: 50%;
    background: var(--brand-blue-bright);
  }
  .back-brand {
    position: absolute;
    left: 29px;
    top: 162px;
    width: 190px;
    text-align: center;
    font-weight: 700;
    color: var(--brand-blue-bright);
    line-height: 1;
  }
  .back-brand .word-main { display: block; font-size: 28px; letter-spacing: 2px; margin-right: -2px; }
  .back-brand .word-sub { display: block; font-size: 9.5px; letter-spacing: 4.6px; margin-right: -4.6px; margin-top: 2px; }
  .divider {
    position: absolute;
    left: 243px;
    top: 54px;
    width: 1px;
    height: 156px;
    background: var(--grey-light);
  }
  .person {
    position: absolute;
    left: 280px;
    top: 62px;
  }
  .person-name { font-size: 19px; font-weight: 700; color: var(--brand-blue); }
  .person-role { font-size: 13px; color: var(--ink); margin-top: 5px; }
  .contact-list {
    position: absolute;
    left: 282px;
    top: 123px;
    list-style: none;
    font-size: 13.5px;
    color: var(--ink);
  }
  .contact-list li { display: flex; align-items: center; height: 18.5px; }
  .contact-list svg { width: 11px; height: 11px; margin-right: 13px; fill: var(--grey); }
  .address {
    position: absolute;
    left: 282px;
    top: 184px;
    font-size: 13.5px;
    color: var(--ink);
  }
  .footer-bands { position: absolute; left: 0; bottom: 0; width: 482px; height: 38px; }
  .back-tagline {
    position: absolute;
    left: 128px; right: 0;
    bottom: 11px;
    text-align: center;
    font-size: 12.5px;
    color: #fff;
  }
</style>
</head>
<body>
  <section class="card card-front">
    <div class="front-name">
      <span class="word-main">VERBROOK</span>
      <span class="word-sub">PROPERTY GROUP</span>
    </div>
    <p class="front-tagline">Construction (Commercial &amp; Industrial) Civil Construction</p>
  </section>

  <section class="card card-back">
    <span class="brand-dot"></span>
    <div class="back-brand">
      <span class="word-main">VERBROOK</span>
      <span class="word-sub">PROPERTY GROUP</span>
    </div>
    <div class="divider"></div>
    <div class="person">
      <p class="person-name">Tomas Verbick</p>
      <p class="person-role">Project Manager</p>
    </div>
    <ul class="contact-list">
      <li><svg viewBox="0 0 12 12"><path d="M1 4 Q6 0 11 4 L9 5 L8 3.5 Q6 3 4 3.5 L3 5 Z M3 6 H9 L10 11 H2 Z"/></svg>(73) 0622 4783</li>
      <li><svg viewBox="0 0 12 12"><path d="M1 2.5 H11 V9.5 H1 Z M1.6 3 L6 6.5 L10.4 3 Z" fill-rule="evenodd"/></svg>(03) 9418 6573</li>
      <li><svg viewBox="0 0 12 12"><circle cx="6" cy="6" r="5"/></svg>info@verbickgroup.com</li>
    </ul>
    <p class="address">41 Barrow Crescent Ashvale 5291</p>
    <svg class="footer-bands" viewBox="0 0 482 38" preserveAspectRatio="none">
      <polygon points="0,24 136,24 132,38 0,38" fill="var(--grey-light)"/>
      <polygon points="142,2 482,2 482,36 118,36" fill="var(--brand-blue)"/>
    </svg>
    <p class="back-tagline">Construction (Commercial &amp; Industrial) Civil Construction</p>
  </section>
</body>
</html>
```